Stylish Business Cards Wanted

- DOUBLE SIDED Design Required -

High end, edgy cards for a corporate and personal stylist. Must include logo,
Name: Belinda Harwick
Title: Director and Stylist
telephone : +61 8 7142 5809
email: belinda@theloombriefing.example
website: theloombriefing.example
Tag: Corporate Workwear & Uniform Specialist | Personal Stylist
Would like nice icons for telephone, email, website

Target Market(s)

Businesses wanting stylish uniforms, people wanting stylish wardrobes

Industry/Entity Type

Corporate Workwear Stylist

Contact Information for Business Card

I would like black, white and gold foiling incorporated in the design - possibly a touch of the other colours on my branding guide attached Name: Belinda Harwick Title: Director and Stylist telephone : +61 8 7142 5809 email: belinda@theloombriefing.example website: theloombriefing.example Tag: Corporate Workwear & Uniform Specialist | Personal Stylist Would like nice icons for telephone, email, website

Font styles to use
Other font styles liked:
• Raleway

Colors

Designer to choose colors to be used in the design.

Requirements
Must have
• Gold foil accents

```html
<!DOCTYPE html>
<html lang="en">
<head>
<meta charset="utf-8">
<title>The Loom Briefing — Business Card</title>
<link rel="stylesheet" href="https://fonts.googleapis.com/css2?family=Arimo:wght@400&display=swap">
<style>
  :root {
    --page: #d8d5d0;
    --card: #f3f2ef;
    --card-edge: #a9a7a3;
    --ink: #333333;
    --band: #373737;
    --band-text: #ffffff;
    --gold: #e6c259;
  }
  html, body {
    margin: 0;
    padding: 0;
    width: 1200px;
    height: 961px;
    overflow: hidden;
    background: var(--page);
    font-family: "Arimo", Arial, sans-serif;
    color: var(--ink);
  }
  .card {
    position: absolute;
    left: 80px;
    top: 179px;
    width: 1040px;
    height: 603px;
    background: var(--card);
    border: 1px dashed var(--card-edge);
    box-sizing: border-box;
  }
  .brand {
    position: absolute;
    left: 135px;
    top: 285px;
    width: 300px;
    text-align: center;
    font-size: 30px;
    line-height: 1;
    letter-spacing: 0.04em;
    color: var(--ink);
    white-space: nowrap;
  }
  .divider {
    position: absolute;
    left: 520px;
    top: 172px;
    width: 1.5px;
    height: 259px;
    background: var(--ink);
  }
  .job-title {
    position: absolute;
    left: 565px;
    top: 182px;
    margin: 0;
    font-size: 30px;
    font-weight: 400;
    line-height: 1;
    color: var(--ink);
    white-space: nowrap;
  }
  .contact-list {
    position: absolute;
    left: 558px;
    top: 272px;
    margin: 0;
    padding: 0;
    list-style: none;
  }
  .contact-item {
    display: flex;
    align-items: center;
    height: 28px;
    margin-bottom: 13px;
    font-size: 23px;
    white-space: nowrap;
  }
  .contact-item:nth-child(2) { margin-bottom: 16px; }
  .contact-icon {
    width: 26px;
    height: 26px;
    margin-right: 12px;
    flex: none;
  }
  .address-band {
    position: absolute;
    left: 0;
    top: 515px;
    width: 995px;
    height: 43px;
    background: var(--band);
    color: var(--band-text);
    font-size: 16px;
    line-height: 43px;
    text-align: center;
  }
  .gold-accent {
    position: absolute;
    left: 1003px;
    top: 515px;
    width: 36px;
    height: 43px;
    background: var(--gold);
  }
</style>
</head>
<body>
  <div class="card">
    <div class="brand">THE LOOM BRIEFING</div>
    <div class="divider"></div>
    <h1 class="job-title">DIRECTOR AND STYLIST</h1>
    <ul class="contact-list">
      <li class="contact-item">
        <svg class="contact-icon" viewBox="0 0 24 24" aria-hidden="true">
          <path fill="#333" d="M6.6 10.8a15.1 15.1 0 0 0 6.6 6.6l2.2-2.2c.3-.3.7-.4 1-.2 1.1.4 2.3.6 3.6.6.6 0 1 .4 1 1V20c0 .6-.4 1-1 1A17 17 0 0 1 3 4c0-.6.4-1 1-1h3.5c.6 0 1 .4 1 1 0 1.3.2 2.5.6 3.6.1.3 0 .7-.2 1l-2.3 2.2z"/>
        </svg>
        <span>+61 8 7142 5809</span>
      </li>
      <li class="contact-item">
        <svg class="contact-icon" viewBox="0 0 24 24" aria-hidden="true">
          <rect x="6.5" y="2" width="11" height="20" rx="1.5" fill="none" stroke="#333" stroke-width="2"/>
          <rect x="8.5" y="5" width="7" height="12" fill="#333"/>
          <circle cx="12" cy="19.5" r="1" fill="#333"/>
        </svg>
        <span>+61 412 508 090</span>
      </li>
      <li class="contact-item">
        <svg class="contact-icon" viewBox="0 0 24 24" aria-hidden="true">
          <rect x="2" y="6" width="20" height="13" fill="none" stroke="#333" stroke-width="1.6"/>
          <path d="M2 6l10 8 10-8M2 19l7.5-7M22 19l-7.5-7" fill="none" stroke="#333" stroke-width="1.6"/>
        </svg>
        <span>belinda@theloombriefing.example</span>
      </li>
      <li class="contact-item">
        <svg class="contact-icon" viewBox="0 0 24 24" aria-hidden="true">
          <g fill="none" stroke="#333" stroke-width="1.5">
            <circle cx="12" cy="12" r="10"/>
            <ellipse cx="12" cy="12" rx="4.5" ry="10"/>
            <path d="M12 2v20M2 12h20M3.5 7h17M3.5 17h17"/>
          </g>
        </svg>
        <span>theloombriefing.example</span>
      </li>
    </ul>
    <div class="address-band">27 Carrick Row Unley, SA, AU</div>
    <div class="gold-accent"></div>
  </div>
</body>
</html>
```